New Business Cards for Tormin Group

We need a new Business Card to compliment our new logo. We are a vibrant design, manufacture and install business providing recreation areas, public parks and Municipal spaces. We want business cards that are classy, modern and clean.

We have recently changed our logo, and are celebrating our 40th anniversary. We want business cards with a new modern design to reflect our status.

Target Market(s)

Customers

Contact Information for Business Card

We need all the details of our 3 offices as per the business card attached. Please disregard the old logo on the business card, the other three files show our new logo.

Requirements
Must have
• All info as per attached business card but with new logo.
Nice to have

```html
<!DOCTYPE html>
<html lang="en">
<head>
<meta charset="utf-8">
<title>Tormin Group – Business Card</title>
<link href="https://fonts.googleapis.com/css2?family=Barlow:wght@400;600;700&display=swap" rel="stylesheet">
<style>
  :root {
    --brand-red: #ec323c;
    --ink-dark: #3c3b3d;
    --ink-text: #4a4a4c;
    --paper: #ffffff;
    --backdrop: #2a2725;
  }
  html, body {
    margin: 0;
    width: 1200px;
    height: 801px;
    overflow: hidden;
    background: var(--backdrop);
    font-family: "Barlow", Arial, sans-serif;
  }
  .card {
    position: absolute;
    left: 100px;
    top: 110px;
    width: 1000px;
    height: 580px;
    background: var(--brand-red);
    overflow: hidden;
    box-shadow: 0 10px 30px rgba(0,0,0,.45);
  }
  .card-shapes { position: absolute; inset: 0; }
  .office {
    position: absolute;
    color: var(--paper);
    font-size: 20px;
    line-height: 27px;
  }
  .office h2 {
    margin: 0;
    font-size: 21px;
    font-weight: 700;
    line-height: 28px;
  }
  .office p { margin: 0; }
  .office .line { display: flex; align-items: center; gap: 10px; }
  .office .line svg { width: 16px; height: 16px; fill: var(--paper); flex: none; }
  .office--head { left: 60px; top: 110px; }
  .office--dubai { left: 60px; top: 275px; }
  .office--qatar { left: 455px; top: 345px; }

  .brand {
    position: absolute;
    right: 50px;
    top: 120px;
    display: flex;
    align-items: center;
    gap: 12px;
    color: var(--ink-dark);
    font-weight: 700;
    font-size: 38px;
    line-height: 44px;
    letter-spacing: 1px;
  }
  .brand-dot {
    width: 34px; height: 34px;
    border-radius: 50%;
    background: var(--brand-red);
  }
  .person {
    position: absolute;
    right: 50px;
    top: 200px;
    text-align: right;
    color: var(--ink-text);
  }
  .person-name {
    margin: 0;
    color: var(--brand-red);
    font-weight: 600;
    font-size: 38px;
    line-height: 42px;
    letter-spacing: 1px;
  }
  .person-role { margin: 0 0 12px; font-size: 22px; line-height: 28px; letter-spacing: 1px; }
  .person .line {
    margin: 0;
    display: flex; justify-content: flex-end; align-items: center; gap: 12px;
    font-size: 19px; line-height: 27px;
  }
  .person .line svg { width: 16px; height: 16px; fill: var(--brand-red); flex: none; }
</style>
</head>
<body>
<svg width="0" height="0" style="position:absolute">
  <defs>
    <symbol id="icon-phone" viewBox="0 0 16 16"><path d="M3 1h3l1.5 4-2 1.3a9 9 0 0 0 4.2 4.2L11 8.5l4 1.5v3a2 2 0 0 1-2 2A12 12 0 0 1 1 3a2 2 0 0 1 2-2z"/></symbol>
    <symbol id="icon-fax" viewBox="0 0 16 16"><path d="M4 1h8v4H4zM1 6h14v6h-3v3H4v-3H1zm4 4v4h6v-4z"/></symbol>
    <symbol id="icon-mail" viewBox="0 0 16 16"><path d="M1 3h14v10H1zm1.5 1.2L8 8.5l5.5-4.3z"/></symbol>
    <symbol id="icon-mobile" viewBox="0 0 16 16"><path d="M4 0h8a1 1 0 0 1 1 1v14a1 1 0 0 1-1 1H4a1 1 0 0 1-1-1V1a1 1 0 0 1 1-1zm1 2v10h6V2z"/></symbol>
    <symbol id="icon-web" viewBox="0 0 16 16"><circle cx="8" cy="8" r="7.5"/></symbol>
  </defs>
</svg>

<main class="card">
  <svg class="card-shapes" viewBox="0 0 1000 580" preserveAspectRatio="none" aria-hidden="true">
    <polygon class="panel-white" points="50,0 1000,0 1000,580" fill="var(--paper)"/>
    <polygon class="accent-stripe" points="26,0 50,0 590,329" fill="var(--ink-dark)"/>
  </svg>

  <section class="office office--head">
    <h2>Head office</h2>
    <p>48213 Abu Dhabi, U.A.E</p>
    <p class="line"><svg><use href="#icon-phone"/></svg>+971 (0)2 5128807</p>
    <p class="line"><svg><use href="#icon-fax"/></svg>+971 (0)2 5128806</p>
    <p class="line"><svg><use href="#icon-mail"/></svg>sales@tormingroup.com</p>
  </section>

  <section class="office office--dubai">
    <h2>Dubai Office</h2>
    <p>517208 Dubai, U.A.E.</p>
    <p class="line"><svg><use href="#icon-phone"/></svg>+971 (0)4 3872410</p>
    <p class="line"><svg><use href="#icon-fax"/></svg>+971 (0)4 3872411</p>
    <p class="line"><svg><use href="#icon-mail"/></svg>sales@tormingroup.com</p>
  </section>

  <section class="office office--qatar">
    <h2>Qatar Office</h2>
    <p>20734 Doha, Qatar</p>
    <p class="line"><svg><use href="#icon-phone"/></svg>+974 40715382</p>
    <p class="line"><svg><use href="#icon-fax"/></svg>+974 40715390</p>
    <p class="line"><svg><use href="#icon-mail"/></svg>sales@tormingroup.com</p>
  </section>

  <div class="brand"><span class="brand-dot"></span>TORMIN GROUP</div>

  <section class="person">
    <h1 class="person-name">Maren Holloway</h1>
    <p class="person-role">Managing Partner</p>
    <p class="line">+971 (0)50 738 4126<svg><use href="#icon-phone"/></svg></p>
    <p class="line">maren@tormingroup.com<svg><use href="#icon-mobile"/></svg></p>
    <p class="line">www.tormingroup.com<svg><use href="#icon-web"/></svg></p>
  </section>
</main>
</body>
</html>
```